1 Dimensional cover for digital product

Please note that if a designer comes in with an original design and other designers try to copy them too closely I will always work with the original designer in order to get the actual look I want.
Therefore it is in the interests of the designers to get their concepts in first.

I am designing some audio products for football (soccer players).

I would like a square version and a 16:9 version of the packaging completed. The square version will be for the Sonvia audio cover and the 16:9 for the thumbnails of videos.

I would like the final images in PSP files as a template that I can change the title and the main image.

I am open to creativity in this project but would like it to be a luxury and premium in what it is portraying.

I have added my logo and also the packaging that I currently use on my sister website which is not aimed at football, soccer.

I've also included an image of one of my models. This would NOT be the product image, but it could be a background image, or you may choose to leave it out altogether.

I've also included an example image as the main product image.

Although I have chosen greyscale I would also like to see products with colour.

The product page is at https://kelvarn.global/collections/all
I add this so that you can chose any one of the titles for this template

Target Market(s)

This is aimed at professional footballers

Industry/Entity Type

Sporting Good

Font styles to use
Serif
Sans Serif

Colors

Designer to choose colors to be used in the design.

Requirements
Must have
• This must look like it is made for an affluent market.
• It may also be simple in its design but I do not wish to be too prescriptive with creativity.
• My typography is Montserrat
Nice to have
• Can include the colors of my logos:
• #5BA9DE
• #272B5F
• Or you can choose to go with greyscale
Should not have
• This is a product for serious athletes so it should look very professional and adult orientated (so not cartoonish its look)

```html
<!DOCTYPE html>
<html lang="en">
<head>
<meta charset="utf-8">
<title>Stress Relief – Hypnosis Sessions Cover</title>
<link rel="stylesheet" href="https://fonts.googleapis.com/css2?family=Montserrat:wght@400;500;800&display=swap">
<style>
  :root {
    --ink-deep: #03060a;
    --panel-dark: #0d1014;
    --panel-glow: #4a4a4c;
    --corner-grey: #c2c3c5;
    --brand-blue: #5BA9DE;
    --brand-navy: #272B5F;
    --gold: #b4a46a;
    --white: #ffffff;
    --photo-top: #2e4454;
    --photo-bottom: #0a1218;
  }
  html, body {
    margin: 0;
    padding: 0;
    width: 1200px;
    height: 676px;
    overflow: hidden;
    background: var(--ink-deep);
  }
  .cover {
    position: relative;
    width: 1200px;
    height: 676px;
    overflow: hidden;
    background: var(--ink-deep);
    font-family: "Montserrat", sans-serif;
  }
  .backdrop {
    position: absolute;
    inset: 0;
  }
  .athlete-photo {
    position: absolute;
    left: 680px;
    top: 76px;
    width: 400px;
    height: 600px;
    border-radius: 48% 48% 0 0 / 22% 22% 0 0;
    background: radial-gradient(ellipse at 50% 30%, var(--photo-top) 0%, #1a2a36 45%, var(--photo-bottom) 100%);
  }
  .brand {
    position: absolute;
    left: 26px;
    top: 30px;
    width: 200px;
    text-align: center;
    color: var(--brand-blue);
    font-weight: 500;
  }
  .brand-dot {
    display: block;
    width: 30px;
    height: 30px;
    margin: 0 auto 12px;
    border-radius: 50%;
    background: var(--brand-navy);
  }
  .brand-name {
    display: block;
    font-size: 9.5px;
    letter-spacing: 0.2px;
    line-height: 1.2;
  }
  .brand-line {
    display: block;
    font-size: 13px;
    letter-spacing: 1.5px;
    margin-top: 3px;
  }
  .eyebrow {
    position: absolute;
    left: 246px;
    top: 242px;
    margin: 0;
    color: var(--white);
    font-weight: 500;
    font-size: 19px;
  }
  .title {
    position: absolute;
    margin: 0;
    color: var(--brand-blue);
    font-weight: 800;
    font-size: 124px;
    line-height: 1;
    letter-spacing: -2px;
  }
  .title-top { left: 237px; top: 268px; }
  .title-bottom { left: 272px; top: 370px; }
  .edition-mark {
    position: absolute;
    left: 241px;
    top: 505px;
    width: 24px;
    height: 24px;
    background: var(--gold);
    transform: rotate(45deg);
  }
  .edition {
    position: absolute;
    left: 298px;
    top: 509px;
    margin: 0;
    color: var(--gold);
    font-weight: 400;
    font-size: 15.5px;
    letter-spacing: 0.3px;
  }
  .tagline {
    position: absolute;
    left: 232px;
    top: 555px;
    margin: 0;
    color: var(--brand-blue);
    font-weight: 400;
    font-size: 13.5px;
    letter-spacing: 0.2px;
  }
</style>
</head>
<body>
  <main class="cover">
    <svg class="backdrop" width="1200" height="676" viewBox="0 0 1200 676" aria-hidden="true">
      <defs>
        <radialGradient id="panelGlow" cx="0.1" cy="0.9" r="0.7">
          <stop offset="0" stop-color="var(--panel-glow)"/>
          <stop offset="0.55" stop-color="#1a1c1f"/>
          <stop offset="1" stop-color="var(--panel-dark)"/>
        </radialGradient>
        <linearGradient id="lightStreak" x1="0" y1="0" x2="1" y2="0">
          <stop offset="0" stop-color="#1e2d38" stop-opacity="0"/>
          <stop offset="0.5" stop-color="#2a4456" stop-opacity="0.55"/>
          <stop offset="1" stop-color="#1e2d38" stop-opacity="0"/>
        </linearGradient>
      </defs>
      <polygon class="left-panel" points="0,0 774,0 102,676 0,676" fill="url(#panelGlow)"/>
      <polygon class="light-streak" points="420,0 640,0 240,400 120,400" fill="url(#lightStreak)"/>
      <polygon class="corner-plate" points="0,0 316,0 119,197 0,78" fill="var(--corner-grey)"/>
    </svg>

    <div class="athlete-photo" role="img" aria-label="Photograph of a young footballer in a dark training top, crouched with hands clasped, looking at the viewer, lit in cool blue tones"></div>

    <div class="brand">
      <span class="brand-dot"></span>
      <span class="brand-name">ALDEN REEVE HYPNOTHERAPY</span>
      <span class="brand-line">KELVARN</span>
    </div>

    <p class="eyebrow">Hypnosis sessions</p>
    <h1 class="title title-top">STRESS</h1>
    <h1 class="title title-bottom">RELIEF</h1>

    <span class="edition-mark"></span>
    <p class="edition">TRIPLE IMPACT EDITION</p>
    <p class="tagline">CONDITION YOURSELF TO A MANAGE A STRESSFUL LIFE</p>
  </main>
</body>
</html>
```